Psychiatric Office Needs a Website- 1st Time Ever!

Been in practice since 2003 with no website, but finally ready to dive in. We are Maplecrest Behavioral Healthcare, a mental health outpatient practice based in Fayetteville, Georgia that sees diverse individuals and families from childhood to advanced age for a variety of conditions. We've grown by word of mouth and referral but would now like to have a digital footprint. Be the pioneer of our website and we will be sure to share. We would like to see designs that are modern, animated, fairly colorful, easy to read, and caters to all ages. Also, we would like the design to take the whole page (not be centered) and can be viewed well on phone/tablet. Please see our outline for more information. Our motto/slogan is: Maplecrest Behavioral Healthcare- A step forward in your wellness journey, so the design should try to reflect that.
Updates

Project Deadline Extended
Reason: site in progress

Target Market(s)

Children through elderly

Industry/Entity Type

Medical

Logo Text

Stepping forward in your wellness journey

Number of Pages Required

1 page

Colors

Designer to choose colors to be used in the design.

Requirements
Must have
• Animation or moving pictures.
• Color.
• Concise.
• User friendly
• Diversity in the stock photos

```html
<!DOCTYPE html>
<html lang="en">
<head>
<meta charset="utf-8">
<title>Maplecrest Behavioral Healthcare</title>
<link href="https://fonts.googleapis.com/css2?family=Lobster&family=Open+Sans:wght@400;600;700&display=swap" rel="stylesheet">
<style>
:root{
  --blue:#2b7fc3;
  --blue-dark:#1f6aa8;
  --cyan:#4ec4dd;
  --cyan-soft:#7fd5e8;
  --green:#7ab648;
  --green-dark:#5f9a34;
  --text:#333;
  --muted:#777;
  --line:#dcdcdc;
  --white:#fff;
}
*{box-sizing:border-box;margin:0;padding:0}
html,body{width:1200px;height:4337px;overflow:hidden}
body{font-family:"Open Sans",Arial,sans-serif;color:var(--text);background:var(--white);position:relative}
.script{font-family:"Lobster",cursive;font-weight:400}
.pill{display:inline-block;background:var(--green);color:var(--white);font-weight:700;font-size:14px;text-transform:uppercase;border-radius:24px;padding:13px 32px;letter-spacing:.3px}
section,header,footer{position:absolute;left:0;width:1200px}

/* header */
.site-header{top:0;height:180px}
.hours-bar{position:absolute;right:0;top:0;width:430px;height:44px;background:var(--blue);clip-path:polygon(30px 0,100% 0,100% 100%,0 100%);color:var(--white);font-size:13px;font-weight:700;display:flex;align-items:center;padding-left:60px;gap:10px}
.brand{position:absolute;left:100px;top:40px;display:flex;align-items:center;gap:14px}
.brand-mark{width:70px;height:70px;border-radius:50%;background:var(--cyan)}
.brand-name{font-family:"Lobster",cursive;color:var(--blue);font-size:26px;line-height:1.15;width:220px}
.contact-row{position:absolute;right:100px;top:72px;display:flex;align-items:center;gap:22px}
.phone{display:flex;align-items:center;gap:8px;color:var(--green);font-weight:700;font-size:14px}
.phone span{color:var(--text)}
.main-nav{position:absolute;right:100px;top:138px;display:flex;gap:34px;font-size:13px;text-transform:uppercase;color:#444}

/* hero */
.hero{top:180px;height:540px}
.hero-photo{position:absolute;inset:0;background:linear-gradient(100deg,#c9c9c9 0%,#b89a80 45%,#c9772f 70%,#7d5a3c 100%)}
.hero-copy{position:absolute;left:100px;top:175px;color:var(--white)}
.hero-copy h1{font-family:"Lobster",cursive;font-weight:400;font-size:46px;line-height:1.2}
.hero-copy p{font-size:23px;margin:8px 0 26px}
.hero-arrow{position:absolute;top:250px;color:rgba(255,255,255,.6);font-size:40px}
.hero-wave{position:absolute;left:0;bottom:0;width:1200px;height:120px}

/* about */
.about{top:720px;height:610px}
.about-copy{position:absolute;left:100px;top:120px;width:590px}
.about-copy h2{font-family:"Lobster",cursive;font-weight:400;font-size:34px;line-height:1}
.about-copy h3{font-family:"Lobster",cursive;font-weight:400;font-size:26px;color:var(--cyan);margin:6px 0 22px}
.about-copy p{font-size:13px;line-height:26px;color:var(--muted);margin-bottom:10px}
.appointment-form{position:absolute;left:722px;top:115px;width:378px;height:400px;border:6px solid #eee;padding:24px 26px}
.appointment-form h4{text-align:center;font-size:20px;font-weight:600;letter-spacing:1px;margin-bottom:20px}
.field{border:1px solid var(--line);height:40px;font-size:12px;color:#999;padding:11px 10px;margin-bottom:12px}
.field-row{display:flex;gap:12px}.field-row .field{flex:1}
.field.message{height:76px}
.submit{background:var(--blue);color:var(--white);text-align:center;font-size:13px;font-weight:700;height:38px;line-height:38px}

/* services */
.services{top:1330px;height:985px;background:linear-gradient(180deg,#4fc6df,#59c3dc)}
.section-title{text-align:center;font-family:"Lobster",cursive;font-weight:400;font-size:40px}
.services .section-title{color:var(--white);position:absolute;top:70px;width:100%}
.card-grid{position:absolute;left:100px;top:155px;display:grid;grid-template-columns:repeat(3,320px);gap:35px 20px}
.service-card{background:var(--white);height:265px;position:relative}
.card-photo{height:190px}
.card-wave{position:absolute;left:0;top:160px;width:320px;height:40px}
.service-card h5{position:absolute;left:0;right:0;top:205px;text-align:center;font-size:13.5px;font-weight:700;text-transform:uppercase;line-height:20px}
.service-card h5 small{text-transform:none;font-weight:400;font-size:11px}
.services .pill{position:absolute;left:50%;transform:translateX(-50%);top:800px}

/* conditions */
.conditions{top:2315px;height:415px}
.conditions .section-title{position:absolute;top:25px;width:100%}
.blue{color:var(--blue)}
.condition{position:absolute;text-align:center;font-size:14px;color:#444}
.condition svg{display:block;margin:0 auto 14px}

/* faq */
.faq{top:2730px;height:435px;background:var(--blue);overflow:hidden}
.faq-photo{position:absolute;left:0;top:0;width:620px;height:435px;background:linear-gradient(135deg,#e9eef2,#b9c8d4 60%,#8fa7bb);clip-path:polygon(0 0,100% 0,70% 100%,0 100%)}
.faq-list{position:absolute;left:660px;top:45px;width:440px}
.faq-list h2{font-family:"Lobster",cursive;font-weight:400;font-size:30px;color:var(--white);margin-bottom:18px}
.faq-item{background:var(--cyan);color:var(--white);font-size:13px;height:40px;line-height:40px;padding:0 14px;margin-bottom:6px;display:flex;justify-content:space-between}
.faq-item b{font-size:18px}
.faq-answer{background:var(--white);color:#555;font-size:13px;height:40px;line-height:40px;padding:0 14px;margin-bottom:6px}
.view-all{text-align:right;color:var(--white);font-size:12px;text-decoration:underline;margin-top:16px}

/* news */
.news{top:3165px;height:625px}
.news .section-title{position:absolute;top:45px;width:100%}
.news-grid{position:absolute;left:100px;top:140px;display:grid;grid-template-columns:repeat(3,320px);gap:20px}
.news-card{border:1px solid #eee;height:400px;position:relative;text-align:center}
.news-card h5{font-size:14px;font-weight:700;margin-top:28px}
.news-card p{font-size:12px;color:var(--muted);line-height:20px;padding:10px 36px}
.news-meta{position:absolute;bottom:18px;left:0;right:0;font-size:12px;color:var(--blue)}

/* footer */
.site-footer{top:3790px;height:547px;background:linear-gradient(180deg,#8bbd5a,#6fa83f);color:var(--white)}
.footer-wave{position:absolute;top:-2px;left:0;width:1200px;height:110px}
.footer-col{position:absolute;top:165px;font-size:12px}
.footer-col h6{font-size:15px;font-weight:700;margin-bottom:26px}
.footer-col li{list-style:none;display:flex;gap:10px;margin-bottom:18px;line-height:18px}
.quick li{margin-bottom:12px}
.email-input{background:var(--white);color:#999;height:34px;width:270px;padding:8px 10px;margin:14px 0 12px}
.subscribe{background:var(--blue);display:inline-block;padding:8px 16px;font-weight:700}
.follow-dot{width:42px;height:42px;border-radius:50%;border:2px solid var(--white)}
.copyright{position:absolute;left:100px;right:100px;top:475px;border-top:1px solid rgba(255,255,255,.4);padding-top:20px;text-align:center;font-size:12px}
</style>
</head>
<body>

<header class="site-header">
  <div class="hours-bar">
    <svg width="16" height="16" viewBox="0 0 16 16"><circle cx="8" cy="8" r="7" fill="none" stroke="#fff" stroke-width="1.6"/><path d="M8 4v4l3 2" stroke="#fff" stroke-width="1.6" fill="none"/></svg>
    OPENING HOURS : MON - SAT : 8.00 - 18.00
  </div>
  <div class="brand"><span class="brand-mark"></span><span class="brand-name">Maplecrest Behavioral Healthcare</span></div>
  <div class="contact-row">
    <div class="phone">
      <svg width="26" height="22" viewBox="0 0 26 22"><rect x="1" y="6" width="24" height="15" rx="3" fill="none" stroke="#7ab648" stroke-width="2"/><path d="M4 7c0-5 18-5 18 0" fill="none" stroke="#7ab648" stroke-width="2"/><circle cx="13" cy="14" r="3" fill="#7ab648"/></svg>
      PHONE : <span>(770) 555-0142</span>
    </div>
    <span class="pill">Patient Portal</span>
  </div>
  <nav class="main-nav"><span>Home</span><span>About Us</span><span>Services</span><span>Conditions We Treat</span><span>New Patients</span><span>Contact Us</span></nav>
</header>

<section class="hero">
  <div class="hero-photo" role="img" aria-label="Photo of a nurse caring for an elderly patient in a wheelchair"></div>
  <span class="hero-arrow" style="left:40px">&#8249;</span><span class="hero-arrow" style="right:40px">&#8250;</span>
  <div class="hero-copy">
    <h1>Maplecrest Behavioral<br>Healthcare</h1>
    <p>A step forward in your wellness journey</p>
    <span class="pill">Take a Screening</span>
  </div>
  <svg class="hero-wave" viewBox="0 0 1200 120" preserveAspectRatio="none">
    <path d="M0 40 Q300 120 650 85 T1200 40 V120 H0Z" fill="#4ec4dd"/>
    <path d="M0 60 Q300 130 650 95 T1200 55 V120 H0Z" fill="#2b7fc3"/>
    <path d="M0 75 Q300 140 650 105 T1200 70 V120 H0Z" fill="#fff"/>
  </svg>
</section>

<section class="about">
  <div class="about-copy">
    <h2>About</h2>
    <h3>Maplecrest Behavioral Healthcare</h3>
    <p>To be the leading provider of outpatient psychiatric care in Atlanta Metro South, working together to promote (the) mental wellness of our community.</p>
    <p>To provide mental health services to children, adults, and the developmentally disabled population that is culturally sensitive regardless of age, race, gender, orientation, religion, or creed. To work hand in hand with clients to overcome mental health challenges and improve their quality of life. To partner with families and caregivers in achieving desired treatment goals for the client. To partner with families and caregivers in achieving desired treatment...</p>
    <span class="pill" style="margin-top:18px">Read More</span>
  </div>
  <div class="appointment-form">
    <h4>APPOINTMENT FORM</h4>
    <div class="field">Your Name</div>
    <div class="field-row"><div class="field">Email</div><div class="field">Phone</div></div>
    <div class="field-row"><div class="field">Day</div><div class="field">Time</div></div>
    <div class="field message">Your Message</div>
    <div class="submit">SUBMIT</div>
  </div>
</section>

<section class="services">
  <h2 class="section-title">Our Services</h2>
  <div class="card-grid">
    <article class="service-card"><div class="card-photo" role="img" aria-label="Photo of a clinician measuring a patient's blood pressure" style="background:linear-gradient(135deg,#8b6a55,#c9a88c)"></div><svg class="card-wave" viewBox="0 0 320 40" preserveAspectRatio="none"><path d="M0 10 Q160 40 320 8 V40 H0Z" fill="#2b7fc3"/><path d="M0 20 Q160 46 320 18 V40 H0Z" fill="#fff"/></svg><h5>Diagnostic Evaluation and<br>Treatment</h5></article>
    <article class="service-card"><div class="card-photo" role="img" aria-label="Photo of a doctor consulting a patient in an office" style="background:linear-gradient(135deg,#dfe6ea,#a9b9c2)"></div><svg class="card-wave" viewBox="0 0 320 40" preserveAspectRatio="none"><path d="M0 10 Q160 40 320 8 V40 H0Z" fill="#2b7fc3"/><path d="M0 20 Q160 46 320 18 V40 H0Z" fill="#fff"/></svg><h5 style="top:215px">Psychopharmacology</h5></article>
    <article class="service-card"><div class="card-photo" role="img" aria-label="Photo of a measuring tape around a waist" style="background:linear-gradient(135deg,#e8d8cc,#c6a893)"></div><svg class="card-wave" viewBox="0 0 320 40" preserveAspectRatio="none"><path d="M0 10 Q160 40 320 8 V40 H0Z" fill="#2b7fc3"/><path d="M0 20 Q160 46 320 18 V40 H0Z" fill="#fff"/></svg><h5>Bariatric Pre-Surgical<br>Consultation <small>(and other surgeries)</small></h5></article>
    <article class="service-card"><div class="card-photo" role="img" aria-label="Photo of a thoughtful young woman resting her chin on her hand" style="background:linear-gradient(135deg,#6b5447,#b18d78)"></div><svg class="card-wave" viewBox="0 0 320 40" preserveAspectRatio="none"><path d="M0 10 Q160 40 320 8 V40 H0Z" fill="#2b7fc3"/><path d="M0 20 Q160 46 320 18 V40 H0Z" fill="#fff"/></svg><h5>Disability and<br>Work-Related Reports <small>(include?)</small></h5></article>
    <article class="service-card"><div class="card-photo" role="img" aria-label="Photo of a child talking with a counselor" style="background:linear-gradient(135deg,#d9c3b0,#b5876a)"></div><svg class="card-wave" viewBox="0 0 320 40" preserveAspectRatio="none"><path d="M0 10 Q160 40 320 8 V40 H0Z" fill="#2b7fc3"/><path d="M0 20 Q160 46 320 18 V40 H0Z" fill="#fff"/></svg><h5>Early Childhood<br>Assessments</h5></article>
    <article class="service-card"><div class="card-photo" role="img" aria-label="Photo of a nurse assisting an elderly man" style="background:linear-gradient(135deg,#cfc6bd,#8e7b6c)"></div><svg class="card-wave" viewBox="0 0 320 40" preserveAspectRatio="none"><path d="M0 10 Q160 40 320 8 V40 H0Z" fill="#2b7fc3"/><path d="M0 20 Q160 46 320 18 V40 H0Z" fill="#fff"/></svg><h5>Substance Abuse<br>Assessments</h5></article>
  </div>
  <span class="pill">View All Services</span>
</section>

<section class="conditions">
  <h2 class="section-title">Conditions <span class="blue">We Treat</span></h2>
  <div class="condition" style="left:95px;top:120px;width:150px">
    <svg width="145" height="145" viewBox="0 0 145 145"><circle cx="72.5" cy="72.5" r="70" fill="none" stroke="#4ec4dd" stroke-width="4"/><circle cx="72.5" cy="72.5" r="56" fill="#4ec4dd"/><path d="M52 95V80c-8-6-8-30 18-32 18 0 24 14 20 22l6 10h-6v8c0 4-4 5-10 5v2" fill="none" stroke="#fff" stroke-width="4"/></svg>
    Mood Disorders</div>
  <div class="condition" style="left:272px;top:120px;width:150px">
    <svg width="145" height="145" viewBox="0 0 145 145"><circle cx="72.5" cy="72.5" r="70" fill="none" stroke="#4ec4dd" stroke-width="4"/><circle cx="72.5" cy="72.5" r="56" fill="#4ec4dd"/><path d="M50 100l14-30 6 10 18-26 8 12" fill="none" stroke="#fff" stroke-width="4"/><circle cx="82" cy="44" r="7" fill="#fff"/></svg>
    Anxiety Disorders</div>
  <div class="condition" style="left:505px;top:100px;width:190px">
    <svg width="185" height="185" viewBox="0 0 185 185"><circle cx="92.5" cy="92.5" r="89" fill="none" stroke="#4ec4dd" stroke-width="5"/><circle cx="92.5" cy="92.5" r="72" fill="#fff" stroke="#4ec4dd" stroke-width="3"/><path d="M92 50c-14 0-14 20 0 34 14-14 14-34 0-34zM92 84l-22 52M92 84l22 52" fill="none" stroke="#4ec4dd" stroke-width="10" stroke-linecap="round"/></svg>
    Common Disorders of<br>Childhood</div>
  <div class="condition" style="left:783px;top:120px;width:150px">
    <svg width="145" height="145" viewBox="0 0 145 145"><circle cx="72.5" cy="72.5" r="70" fill="none" stroke="#4ec4dd" stroke-width="4"/><circle cx="72.5" cy="72.5" r="56" fill="#4ec4dd"/><path d="M52 98V82c-8-6-8-32 20-34 18 0 24 14 20 22l6 10h-6v8c0 4-4 5-10 5v5" fill="none" stroke="#fff" stroke-width="4"/><circle cx="72" cy="66" r="9" fill="none" stroke="#fff" stroke-width="3"/></svg>
    Psychotic Disorders</div>
  <div class="condition" style="left:960px;top:120px;width:150px">
    <svg width="145" height="145" viewBox="0 0 145 145"><circle cx="72.5" cy="72.5" r="70" fill="none" stroke="#4ec4dd" stroke-width="4"/><circle cx="72.5" cy="72.5" r="56" fill="#4ec4dd"/><circle cx="72.5" cy="52" r="10" fill="#fff"/><path d="M48 96c0-18 10-28 24.5-28S97 78 97 96z" fill="#fff"/><path d="M44 80h57" stroke="#4ec4dd" stroke-width="5"/></svg>
    Eating Disorders</div>
</section>

<section class="faq">
  <div class="faq-photo" role="img" aria-label="Photo of a doctor with a stethoscope holding a clipboard"></div>
  <div class="faq-list">
    <h2>Frequently Asked Questions</h2>
    <div class="faq-item">What do I need to bring with me to my first visit?<b>&#8722;</b></div>
    <div class="faq-answer">Insurance card, patient forms found on our Form's page.</div>
    <div class="faq-item">How long do I have to wait to be seen?<b>+</b></div>
    <div class="faq-item">What type of insurance do you accept?<b>+</b></div>
    <div class="faq-item">Why is my child not doing well in school?<b>+</b></div>
    <div class="faq-item">I feel sad/tired and I do not have energy is that normal?<b>+</b></div>
    <div class="view-all">View All &gt;&gt;</div>
  </div>
</section>

<section class="news">
  <h2 class="section-title">Latest <span class="blue">News &amp; Tips</span></h2>
  <div class="news-grid">
    <article class="news-card"><div class="card-photo" role="img" aria-label="Photo of a hand reaching out" style="background:linear-gradient(135deg,#f1f1f1,#cfcfcf)"></div><svg class="card-wave" viewBox="0 0 320 40" preserveAspectRatio="none"><path d="M0 10 Q160 40 320 8 V40 H0Z" fill="#2b7fc3"/><path d="M0 20 Q160 46 320 18 V40 H0Z" fill="#fff"/></svg><h5>CIRCUMSTANCES OCCUR INOILA</h5><p>Sed ut perspiciatis unde omnis iste natus error sit voluptatem accusantium doloremque</p><div class="news-meta">&#128197; March 12,2017 &nbsp;|&nbsp; 6 comments &nbsp;|&nbsp; 3</div></article>
    <article class="news-card"><div class="card-photo" role="img" aria-label="Photo of a doctor talking with a patient" style="background:linear-gradient(135deg,#e6eef2,#a7bccb)"></div><svg class="card-wave" viewBox="0 0 320 40" preserveAspectRatio="none"><path d="M0 10 Q160 40 320 8 V40 H0Z" fill="#2b7fc3"/><path d="M0 20 Q160 46 320 18 V40 H0Z" fill="#fff"/></svg><h5>SED QUIA NON NUMQUAM EIUS</h5><p>Sed ut perspiciatis unde omnis iste natus error sit voluptatem accusantium doloremque</p><div class="news-meta" style="color:var(--green)">&#128197; March 12,2017 &nbsp;|&nbsp; 6 comments &nbsp;|&nbsp; 3</div></article>
    <article class="news-card"><div class="card-photo" role="img" aria-label="Photo of a therapist in session with a client" style="background:linear-gradient(135deg,#d9d3cc,#8f8276)"></div><svg class="card-wave" viewBox="0 0 320 40" preserveAspectRatio="none"><path d="M0 10 Q160 40 320 8 V40 H0Z" fill="#2b7fc3"/><path d="M0 20 Q160 46 320 18 V40 H0Z" fill="#fff"/></svg><h5>QUIS NOSTRUD EXERULLAMCO</h5><p>Sed ut perspiciatis unde omnis iste natus error sit voluptatem accusantium doloremque</p><div class="news-meta">&#128197; March 12,2017 &nbsp;|&nbsp; 6 comments &nbsp;|&nbsp; 3</div></article>
  </div>
</section>

<footer class="site-footer">
  <svg class="footer-wave" viewBox="0 0 1200 110" preserveAspectRatio="none">
    <path d="M0 0H1200V40Q850 100 450 55T0 60Z" fill="#fff"/>
    <path d="M0 60Q450 55 450 55T1200 40V52Q850 112 450 67T0 72Z" fill="#2b7fc3"/>
    <path d="M0 72Q450 67 450 67T1200 52V62Q850 122 450 77T0 82Z" fill="#4ec4dd"/>
  </svg>
  <div class="footer-col" style="left:115px;width:260px">
    <h6>CONTACT US</h6>
    <ul>
      <li><span>&#8962;</span>1716 Peachtree Lane, Fayetteville, GA</li>
      <li><span>&#9742;</span>Call Us : (770) 555-0142</li>
      <li><span>&#9719;</span>Hours : Mon-Sat (8.00 to 18.00)</li>
      <li><span>&#9993;</span>hello@maplecrest.example</li>
    </ul>
  </div>
  <div class="footer-col quick" style="left:415px">
    <h6>QUICK LINKS</h6>
    <ul><li>&#8250; Home</li><li>&#8250; About Us</li><li>&#8250; Services</li><li>&#8250; Conditions We Treat</li><li>&#8250; New Patients</li><li>&#8250; Contact Us</li></ul>
  </div>
  <div class="footer-col" style="left:635px">
    <h6>SIGN UP NEWSLETTER</h6>
    <p style="width:250px;line-height:18px">Get practice news and wellness tips sent to your inbox.</p>
    <div class="email-input">Enter email...</div>
    <span class="subscribe">SUBSCRIBE</span>
  </div>
  <div class="footer-col" style="left:975px">
    <h6>FOLLOW US</h6>
    <div class="follow-dot"></div>
  </div>
  <div class="copyright">&copy; copyright 2017 Maplecrest Behavioral Healthcare. All rights reserved &nbsp;|&nbsp; Privacy policy</div>
</footer>

</body>
</html>
```